Stylish new business card needed!

Hello everyone! I am in need of a new business card design for an alarm company here in Hurricane WV. I have all fonts, color codes and logos provided for you use! We are a young company and like the style of a clean sleek looking business card. Would like it double sided, one side holding the logo and the other with your design!
Target Market(s)
The people that are looking for the newest tech for home automation and security
Industry/Entity Type
Alarm services; Home automation
Contact Information for Business Card
Name of person; position (Sales; Installer); Phone Number (555.418.7260); Employee cell Number; Website (www.GuardedByVelk.example); Employee Email; Double sided
Look and feel
Each slider illustrates characteristics of the customer's brand and the style your logo design should communicate.

```html
<!DOCTYPE html>
<html lang="en">
<head>
<meta charset="utf-8">
<title>Velk Business Card</title>
<link rel="stylesheet" href="https://fonts.googleapis.com/css2?family=Lato:wght@300;400;700;900&display=swap">
<style>
  :root {
    --bg: #1f2023;
    --card: #2d2d2f;
    --orange: #f28a35;
    --grey: #9a9a9a;
    --text-grey: #a8a8a8;
  }
  * { margin: 0; padding: 0; box-sizing: border-box; }
  html, body { width: 1200px; height: 952px; overflow: hidden; background: var(--bg); }
  body { position: relative; font-family: "Lato", sans-serif; }
  .card {
    position: absolute;
    top: 327px;
    width: 520px;
    height: 298px;
    background: var(--card);
    border-radius: 22px;
    overflow: hidden;
    box-shadow: 0 18px 40px rgba(0,0,0,.45);
  }
  .card--front { left: 60px; }
  .card--back { left: 620px; }
  .stripe { position: absolute; left: 0; width: 100%; height: 20px; }
  .card--front .stripe { top: 258px; }
  .card--back .stripe { top: 30px; }

  .wordmark {
    position: absolute;
    font-weight: 300;
    color: var(--grey);
    letter-spacing: 4px;
    line-height: 1;
    display: flex;
    align-items: center;
    gap: 14px;
  }
  .wordmark__dot { width: 14px; height: 14px; border-radius: 50%; background: var(--orange); }
  .card--front .wordmark { left: 200px; top: 52px; font-size: 78px; }
  .card--back .wordmark { left: 0; right: 0; justify-content: center; top: 100px; font-size: 82px; }

  .tagline {
    position: absolute;
    left: 0; right: 0; top: 196px;
    text-align: center;
    font-size: 10px;
    font-weight: 900;
    letter-spacing: 1px;
    color: var(--orange);
  }

  .person { position: absolute; left: 34px; top: 150px; }
  .person__name { font-size: 19px; color: var(--orange); letter-spacing: .5px; }
  .person__name strong { font-weight: 900; }
  .person__role { margin-top: 4px; font-size: 14px; color: var(--text-grey); }

  .contacts { position: absolute; left: 238px; top: 146px; list-style: none; }
  .contacts li { display: flex; align-items: center; gap: 9px; font-size: 14px; color: var(--text-grey); margin-bottom: 9px; }
  .icon { width: 18px; height: 18px; border-radius: 3px; background: var(--orange); display: flex; align-items: center; justify-content: center; }
</style>
</head>
<body>

<section class="card card--front">
  <svg class="stripe" viewBox="0 0 520 20" preserveAspectRatio="none" aria-hidden="true">
    <rect x="0" y="3" width="160" height="3" fill="#9a9a9a"/>
    <polygon points="160,3 166,3 172,10 166,10" fill="#9a9a9a"/>
    <rect x="168" y="10" width="352" height="5" fill="#f28a35"/>
  </svg>
  <div class="wordmark">VELK<span class="wordmark__dot"></span></div>
  <div class="person">
    <p class="person__name">DANIEL R. <strong>MERCER</strong></p>
    <p class="person__role">Managing Director</p>
  </div>
  <ul class="contacts">
    <li>
      <span class="icon"><svg width="11" height="11" viewBox="0 0 24 24"><path fill="#fff" d="M6.6 10.8a15 15 0 0 0 6.6 6.6l2.2-2.2a1 1 0 0 1 1-.25 11.4 11.4 0 0 0 3.6.57 1 1 0 0 1 1 1V20a1 1 0 0 1-1 1A17 17 0 0 1 3 4a1 1 0 0 1 1-1h3.5a1 1 0 0 1 1 1c0 1.25.2 2.45.57 3.57a1 1 0 0 1-.25 1z"/></svg></span>
      555.418.7260
    </li>
    <li>
      <span class="icon"><svg width="11" height="11" viewBox="0 0 24 24"><path fill="none" stroke="#fff" stroke-width="2.4" d="M3 6h18v12H3zM3 6l9 7 9-7"/></svg></span>
      office@velkmail.example
    </li>
    <li>
      <span class="icon"><svg width="11" height="11" viewBox="0 0 24 24"><path fill="#fff" d="M5 3l14 8-6 1.5 3.5 7-2.5 1.2-3.5-7L6 18z"/></svg></span>
      www.GuardedByVelk.example
    </li>
  </ul>
</section>

<section class="card card--back">
  <svg class="stripe" viewBox="0 0 520 20" preserveAspectRatio="none" aria-hidden="true">
    <rect x="0" y="3" width="170" height="5" fill="#f28a35"/>
    <polygon points="170,3 176,3 182,12 176,12" fill="#f28a35"/>
    <rect x="178" y="10" width="342" height="3" fill="#9a9a9a"/>
  </svg>
  <div class="wordmark">VELK<span class="wordmark__dot"></span></div>
  <p class="tagline">AUTOMATION AND SECURITY SERVICES</p>
</section>

</body>
</html>
```